Redesign 2016 Digital Marketing Website and Convert to Wordpress

Technology needed to integrate:

- redesign and convert to wordpress
- gravity forms
- malware and hacker defense / honeypot (must be very secure from hackers)
- I want gravity forms to be a flow that asks many questions with icons and progress bar.
- 1 home page design
- 1 blog design
- 1 design for internal page content
- 1 multi step gravity form
I want to focus on SMB's. We are a marketing agency thats been around since 2016.

Site is: tallpine.agency

I am looking to redesign the homepage, blog page and services page. The services page will be a template for all inner pages of the site. All content needs to be moved into the new design.

I want to get ride of the weird video.

I need you to install gravity forms pro model so we can pass utms.

I need the gravity form to be a multi step form with icons.

All "contact us" or "get a free assesments" call to actions will go to this form only.

step 1:
what is your website

step 2:
what industry are you in
- option
- Home Services
- Legal
- Ecommerce
- Lead Gen

No matter which one they select its going to produce a differnt calculator for them.

Law:
How many leads did you get last month
how much is each ase worth on average
How much revenue do you want to make

Home servicse:
How many bookings did you get last month
How much is each service worht on average
How much revenue do you wangt to make

Ecommerce:
What is your average order value
How muny purchases did you have last month
How much revenue did you drive
How much revenue do you want to drive

For lead gen:
How many leads did you get lawt month
How much revenue did they generate

Step 3:
What is your current advertising budget

step 4:
Do you have a CRM and if so what is it

Step 5:
What is your personal informagtion
name
email
phone

Let me know if this is enough to get you going

Small and medium sized law firms, ecommerce, home services and lead gen customers.

We are a digital marketing agency

• Use whats on the current site and improve upon it

• Must be very secure, developed into a wordpress website. using gravity forms. remove my photo and my staffs photo, depersonalize it so it doesnt mention me or sam crolley. Use the same color scheme. I am looking to redesign the homepage, blog page and services page. The services page will be a template for all inner pages of the site. All content needs to be moved into the new design. I want to get ride of the weird video. I need you to install gravity forms pro model so we can pass utms. I need the gravity form to be a multi step form with icons. All "contact us" or "get a free assesments" call to actions will go to this form only. step 1: what is your website step 2: what industry are you in - option - Home Services - Legal - Ecommerce - Lead Gen No matter which one they select its going to produce a differnt calculator for them. Law: How many leads did you get last month how much is each ase worth on average How much revenue do you want to make Home servicse: How many bookings did you get last month How much is each service worht on average How much revenue do you wangt to make Ecommerce: What is your average order value How muny purchases did you have last month How much revenue did you drive How much revenue do you want to drive For lead gen: How many leads did you get lawt month How much revenue did they generate How much revenue do you want to make Step 3: What is your current advertising budget step 4: Do you have a CRM and if so what is it Step 5: What is your personal informagtion name email phone Let me know if this is enough to get you going
• SHOULD NOT BE SLOPPY, I AM LOOKING FOR ATTENTION TO DETAIL.

```html
<!DOCTYPE html>
<html lang="en">
<head>
<meta charset="utf-8">
<title>Industries We Love Working With | Tall Pine Growth Marketing</title>
<link href="https://fonts.googleapis.com/css2?family=Montserrat:wght@400;600;700;800&family=Roboto:wght@400;500;700&display=swap" rel="stylesheet">
<style>
:root{
  --brand:#6b1217;
  --brand-bright:#8a1c22;
  --blush:#fbe0e1;
  --ink:#1f1f1f;
  --muted:#6d6d6d;
  --line:#e6e6e6;
  --nav:#222222;
  --footer:#232323;
  --white:#ffffff;
}
*{box-sizing:border-box;margin:0;padding:0}
html,body{width:1200px;height:3847px;overflow:hidden}
body{font-family:'Roboto',sans-serif;color:var(--ink);background:var(--white);position:relative}
a{color:inherit;text-decoration:none}

/* Top bar */
.topbar{height:75px;position:relative}
.brand{position:absolute;left:143px;top:14px;display:flex;align-items:center;gap:14px}
.brand-mark{width:46px;height:46px;border-radius:50%;background:var(--brand)}
.brand-name{font-family:'Montserrat',sans-serif;font-size:19px;font-weight:400;color:var(--brand);letter-spacing:1.5px;line-height:1}
.brand-tag{font-family:'Montserrat',sans-serif;font-size:7px;letter-spacing:3.2px;color:var(--brand);margin-top:6px}
.call{position:absolute;left:604px;top:28px;font-size:12px;font-weight:700;color:var(--ink);display:flex;align-items:baseline;gap:9px}
.call .phone{font-size:16px;font-weight:500;color:var(--brand-bright)}
.cta{position:absolute;left:862px;top:16px;width:193px;height:43px;border-radius:22px;background:var(--brand);color:var(--white);font-size:14px;font-weight:500;display:flex;align-items:center;justify-content:center}

/* Nav */
.mainnav{height:42px;background:var(--nav)}
.mainnav ul{list-style:none;display:flex;height:42px;align-items:center;position:relative}
.mainnav li{position:absolute;transform:translateX(-50%);color:var(--white);font-size:13px;font-weight:700;text-transform:uppercase;white-space:nowrap}

/* Hero */
.hero{height:355px;background:var(--brand);color:var(--white);text-align:center;padding-top:98px}
.hero h1{font-family:'Montserrat',sans-serif;font-size:43px;font-weight:400;letter-spacing:.3px;line-height:1}
.hero h1 strong{font-weight:800}
.hero p{margin:32px auto 0;width:760px;font-size:15.5px;font-weight:500;line-height:27px}

/* Industries grid */
.industries{position:absolute;left:143px;top:557px;width:914px;display:grid;grid-template-columns:repeat(3,286px);column-gap:28px;row-gap:33px}
.card{height:260px;border:1px solid var(--line);border-radius:3px;padding:36px 22px 0;background:var(--white)}
.card.is-active{box-shadow:0 8px 28px rgba(0,0,0,.10);border-color:#eee}
.card-icon{position:relative;width:96px;height:66px}
.card-icon .halo{position:absolute;left:36px;top:3px;width:58px;height:58px;border-radius:50%;background:var(--blush)}
.card-icon .art{position:absolute;left:0;top:0;width:58px;height:58px;border-radius:8px;background:linear-gradient(135deg,rgba(107,18,23,.85),rgba(107,18,23,.45));opacity:.9}
.card h2{margin-top:24px;font-size:17.5px;font-weight:700;color:var(--ink)}
.card p{margin-top:12px;font-size:13px;line-height:21px;color:var(--muted);height:42px;overflow:hidden}
.card .more{display:inline-flex;align-items:center;gap:6px;margin-top:12px;font-size:12.5px;font-weight:700;color:var(--brand-bright);text-transform:uppercase}

/* Footer */
.site-footer{position:absolute;left:0;top:3541px;width:1200px;height:306px;background:var(--footer);color:var(--white)}
.foot-brand{position:absolute;left:143px;top:80px;display:flex;align-items:center;gap:18px}
.foot-brand .brand-mark{width:58px;height:58px}
.foot-brand .brand-name{color:var(--white);font-size:25px;letter-spacing:2px}
.foot-brand .brand-tag{color:var(--white);font-size:8.5px;letter-spacing:4.2px;margin-top:8px}
.social{position:absolute;left:196px;top:164px;display:flex;gap:11px}
.social span{width:37px;height:37px;border:1.5px solid var(--white);border-radius:50%}
.divider{position:absolute;top:52px;width:3px;height:48px;background:var(--brand-bright)}
.foot-col h3{font-size:14.5px;font-weight:700;text-transform:uppercase;margin-bottom:18px}
.links{position:absolute;left:538px;top:55px}
.links ul{list-style:none}
.links li{font-size:13px;line-height:21px}
.contact{position:absolute;left:810px;top:55px}
.contact .row{display:flex;gap:12px;font-size:13.5px;font-weight:500;line-height:22px;margin-bottom:12px}
.contact svg{flex:0 0 18px;margin-top:3px}
.contact .tel{font-size:15px;font-weight:700;text-decoration:underline}
.footbar{position:absolute;left:143px;right:143px;top:240px;border-top:1px solid #3b3b3b;display:flex;justify-content:space-between;padding-top:26px;font-size:12.5px}
.legal{display:flex;gap:14px}
</style>
</head>
<body>

<header class="topbar">
  <a class="brand" href="#">
    <span class="brand-mark"></span>
    <span><div class="brand-name">TALL PINE</div><div class="brand-tag">GROWTH MARKETING</div></span>
  </a>
  <div class="call">OR CALL US NOW: <span class="phone">(480) 555-0142</span></div>
  <a class="cta" href="#">Get a Free Consultation</a>
</header>

<nav class="mainnav">
  <ul>
    <li style="left:176px">Home</li>
    <li style="left:274px">About Us</li>
    <li style="left:407px">Our Industries</li>
    <li style="left:555px">Our Services</li>
    <li style="left:686px">Resources</li>
    <li style="left:802px">Training</li>
    <li style="left:896px">Blog</li>
    <li style="left:1000px">Contact Us</li>
  </ul>
</nav>

<section class="hero">
  <h1><strong>INDUSTRIES WE</strong> LOVE WORKING WITH</h1>
  <p>We are quick to admit what industries we have a tremendous amount of success and experience in. We have success and trail blaze tra-digital marketing across many verticals and below are some of the ones we think you should know about.</p>
</section>

<main class="industries">
  <article class="card is-active"><div class="card-icon"><span class="halo"></span><span class="art" role="img" aria-label="Line illustration of a graduation cap on books"></span></div><h2>Education</h2><p>We have worked with some pretty major players in the education space</p><a class="more" href="#">Learn More <svg width="8" height="8" viewBox="0 0 8 8"><path d="M1 1l3 3-3 3M4 1l3 3-3 3" fill="none" stroke="currentColor" stroke-width="1.3"/></svg></a></article>
  <article class="card"><div class="card-icon"><span class="halo"></span><span class="art" role="img" aria-label="Line illustration of scales of justice in a hand"></span></div><h2>Lawyers</h2><p>We have worked with high profile lawyers for years, understand</p><a class="more" href="#">Learn More <svg width="8" height="8" viewBox="0 0 8 8"><path d="M1 1l3 3-3 3M4 1l3 3-3 3" fill="none" stroke="currentColor" stroke-width="1.3"/></svg></a></article>
  <article class="card"><div class="card-icon"><span class="halo"></span><span class="art" role="img" aria-label="Line illustration of hands holding a medical heart"></span></div><h2>Healthcare Marketing</h2><p>We have deep knowledge of the medical, patient care and pain</p><a class="more" href="#">Learn More <svg width="8" height="8" viewBox="0 0 8 8"><path d="M1 1l3 3-3 3M4 1l3 3-3 3" fill="none" stroke="currentColor" stroke-width="1.3"/></svg></a></article>

  <article class="card"><div class="card-icon"><span class="halo"></span><span class="art" role="img" aria-label="Line illustration for cosmetic surgery"></span></div><h2>Cosmetic Surgery Center</h2><p>Cosmetic Surgery is a multi billion dollar industry that demands a unique</p><a class="more" href="#">Learn More <svg width="8" height="8" viewBox="0 0 8 8"><path d="M1 1l3 3-3 3M4 1l3 3-3 3" fill="none" stroke="currentColor" stroke-width="1.3"/></svg></a></article>
  <article class="card"><div class="card-icon"><span class="halo"></span><span class="art" role="img" aria-label="Line illustration of a tooth and dental tool"></span></div><h2>Dental Marketing</h2><p>We are familiar with the different CDP's a dental office uses</p><a class="more" href="#">Learn More <svg width="8" height="8" viewBox="0 0 8 8"><path d="M1 1l3 3-3 3M4 1l3 3-3 3" fill="none" stroke="currentColor" stroke-width="1.3"/></svg></a></article>
  <article class="card"><div class="card-icon"><span class="halo"></span><span class="art" role="img" aria-label="Line illustration of a foot"></span></div><h2>Podiatrist Marketing</h2><p>We have deep knowledge of the podiatrist medical service space.</p><a class="more" href="#">Learn More <svg width="8" height="8" viewBox="0 0 8 8"><path d="M1 1l3 3-3 3M4 1l3 3-3 3" fill="none" stroke="currentColor" stroke-width="1.3"/></svg></a></article>

  <article class="card"><div class="card-icon"><span class="halo"></span><span class="art" role="img" aria-label="Line illustration representing back pain"></span></div><h2>Pain Center Marketing</h2><p>There are specific legalities and restrictions around health care</p><a class="more" href="#">Learn More <svg width="8" height="8" viewBox="0 0 8 8"><path d="M1 1l3 3-3 3M4 1l3 3-3 3" fill="none" stroke="currentColor" stroke-width="1.3"/></svg></a></article>
  <article class="card"><div class="card-icon"><span class="halo"></span><span class="art" role="img" aria-label="Line illustration of plumbing tools"></span></div><h2>Plumber Marketing</h2><p>When plumbers experience a clog in their marketing funnel</p><a class="more" href="#">Learn More <svg width="8" height="8" viewBox="0 0 8 8"><path d="M1 1l3 3-3 3M4 1l3 3-3 3" fill="none" stroke="currentColor" stroke-width="1.3"/></svg></a></article>
  <article class="card"><div class="card-icon"><span class="halo"></span><span class="art" role="img" aria-label="Line illustration of a hard hat and tools"></span></div><h2>Marketing For Contractors</h2><p>We have deep knowledge of the contractor industry</p><a class="more" href="#">Learn More <svg width="8" height="8" viewBox="0 0 8 8"><path d="M1 1l3 3-3 3M4 1l3 3-3 3" fill="none" stroke="currentColor" stroke-width="1.3"/></svg></a></article>

  <article class="card"><div class="card-icon"><span class="halo"></span><span class="art" role="img" aria-label="Line illustration of storefronts"></span></div><h2>Marketing For Franchises</h2><p>We have deep knowledge of the Franchise industry.</p><a class="more" href="#">Learn More <svg width="8" height="8" viewBox="0 0 8 8"><path d="M1 1l3 3-3 3M4 1l3 3-3 3" fill="none" stroke="currentColor" stroke-width="1.3"/></svg></a></article>
  <article class="card"><div class="card-icon"><span class="halo"></span><span class="art" role="img" aria-label="Line illustration of a landscaped yard"></span></div><h2>Marketing For Landscapers</h2><p>Landscaping is a service in massive demand as a recurring need,</p><a class="more" href="#">Learn More <svg width="8" height="8" viewBox="0 0 8 8"><path d="M1 1l3 3-3 3M4 1l3 3-3 3" fill="none" stroke="currentColor" stroke-width="1.3"/></svg></a></article>
  <article class="card"><div class="card-icon"><span class="halo"></span><span class="art" role="img" aria-label="Line illustration of a car with a gear"></span></div><h2>Automotive Repair Marketing</h2><p>From auto repair and service to auto dealerships, Tall Pine</p><a class="more" href="#">Learn More <svg width="8" height="8" viewBox="0 0 8 8"><path d="M1 1l3 3-3 3M4 1l3 3-3 3" fill="none" stroke="currentColor" stroke-width="1.3"/></svg></a></article>

  <article class="card"><div class="card-icon"><span class="halo"></span><span class="art" role="img" aria-label="Line illustration of a house"></span></div><h2>Home Services</h2><p>We have deep knowledge of the home services industry.</p><a class="more" href="#">Learn More <svg width="8" height="8" viewBox="0 0 8 8"><path d="M1 1l3 3-3 3M4 1l3 3-3 3" fill="none" stroke="currentColor" stroke-width="1.3"/></svg></a></article>
  <article class="card"><div class="card-icon"><span class="halo"></span><span class="art" role="img" aria-label="Line illustration of a shopping cart with a globe"></span></div><h2>Ecommerce</h2><p>We have deep knowledge of the online retail and ecommerce space.</p><a class="more" href="#">Learn More <svg width="8" height="8" viewBox="0 0 8 8"><path d="M1 1l3 3-3 3M4 1l3 3-3 3" fill="none" stroke="currentColor" stroke-width="1.3"/></svg></a></article>
  <article class="card"><div class="card-icon"><span class="halo"></span><span class="art" role="img" aria-label="Line illustration of a restaurant front"></span></div><h2>Restaurants</h2><p>We love the restaurant industry. We have deep knowledge of the restaurant</p><a class="more" href="#">Learn More <svg width="8" height="8" viewBox="0 0 8 8"><path d="M1 1l3 3-3 3M4 1l3 3-3 3" fill="none" stroke="currentColor" stroke-width="1.3"/></svg></a></article>

  <article class="card"><div class="card-icon"><span class="halo"></span><span class="art" role="img" aria-label="Line illustration of coins and a rising chart"></span></div><h2>Financial Services</h2><p>We have deep knowledge of the financial services industry.</p><a class="more" href="#">Learn More <svg width="8" height="8" viewBox="0 0 8 8"><path d="M1 1l3 3-3 3M4 1l3 3-3 3" fill="none" stroke="currentColor" stroke-width="1.3"/></svg></a></article>
  <article class="card"><div class="card-icon"><span class="halo"></span><span class="art" role="img" aria-label="Line illustration of a builder in a house outline"></span></div><h2>Home Builders</h2><p>Home builders have never had more success in their marketing</p><a class="more" href="#">Learn More <svg width="8" height="8" viewBox="0 0 8 8"><path d="M1 1l3 3-3 3M4 1l3 3-3 3" fill="none" stroke="currentColor" stroke-width="1.3"/></svg></a></article>
  <article class="card"><div class="card-icon"><span class="halo"></span><span class="art" role="img" aria-label="Line illustration of a fire extinguisher and flame"></span></div><h2>Fire Protection</h2><p>Fire protection is typically overlooked from a consumer perspective.</p><a class="more" href="#">Learn More <svg width="8" height="8" viewBox="0 0 8 8"><path d="M1 1l3 3-3 3M4 1l3 3-3 3" fill="none" stroke="currentColor" stroke-width="1.3"/></svg></a></article>

  <article class="card"><div class="card-icon"><span class="halo"></span><span class="art" role="img" aria-label="Line illustration of an electrician with a plug"></span></div><h2>Electricians</h2><p>We have deep knowledge of the electrician industry.</p><a class="more" href="#">Learn More <svg width="8" height="8" viewBox="0 0 8 8"><path d="M1 1l3 3-3 3M4 1l3 3-3 3" fill="none" stroke="currentColor" stroke-width="1.3"/></svg></a></article>
  <article class="card"><div class="card-icon"><span class="halo"></span><span class="art" role="img" aria-label="Line illustration of an HVAC unit"></span></div><h2>HVAC Marketing</h2><p>We have worked with some of the biggest names in the HVAC industry</p><a class="more" href="#">Learn More <svg width="8" height="8" viewBox="0 0 8 8"><path d="M1 1l3 3-3 3M4 1l3 3-3 3" fill="none" stroke="currentColor" stroke-width="1.3"/></svg></a></article>
  <article class="card"><div class="card-icon"><span class="halo"></span><span class="art" role="img" aria-label="Line illustration of hands holding a shield"></span></div><h2>Insurance Agencies</h2><p>Insurance agents need marketing too and if you are looking for a marketing</p><a class="more" href="#">Learn More <svg width="8" height="8" viewBox="0 0 8 8"><path d="M1 1l3 3-3 3M4 1l3 3-3 3" fill="none" stroke="currentColor" stroke-width="1.3"/></svg></a></article>

  <article class="card"><div class="card-icon"><span class="halo"></span><span class="art" role="img" aria-label="Line illustration of pest spraying"></span></div><h2>Pest Control Marketing</h2><p>You control the pests and we will drive the rest. From local citations, content</p><a class="more" href="#">Learn More <svg width="8" height="8" viewBox="0 0 8 8"><path d="M1 1l3 3-3 3M4 1l3 3-3 3" fill="none" stroke="currentColor" stroke-width="1.3"/></svg></a></article>
  <article class="card"><div class="card-icon"><span class="halo"></span><span class="art" role="img" aria-label="Line illustration of roof tiles"></span></div><h2>Roofers</h2><p>The roofing industry is competitive and most roofers don't have a full funnel</p><a class="more" href="#">Learn More <svg width="8" height="8" viewBox="0 0 8 8"><path d="M1 1l3 3-3 3M4 1l3 3-3 3" fill="none" stroke="currentColor" stroke-width="1.3"/></svg></a></article>
  <article class="card"><div class="card-icon"><span class="halo"></span><span class="art" role="img" aria-label="Line illustration of a house with a wrench"></span></div><h2>Remodelers</h2><p>Remodelers have grown their business by 10x by leveraging our marketing</p><a class="more" href="#">Learn More <svg width="8" height="8" viewBox="0 0 8 8"><path d="M1 1l3 3-3 3M4 1l3 3-3 3" fill="none" stroke="currentColor" stroke-width="1.3"/></svg></a></article>

  <article class="card"><div class="card-icon"><span class="halo"></span><span class="art" role="img" aria-label="Line illustration of a house held in a hand"></span></div><h2>Real Estate</h2><p>We have worked in the real estate industry for 17 years and have a long</p><a class="more" href="#">Learn More <svg width="8" height="8" viewBox="0 0 8 8"><path d="M1 1l3 3-3 3M4 1l3 3-3 3" fill="none" stroke="currentColor" stroke-width="1.3"/></svg></a></article>
  <article class="card"><div class="card-icon"><span class="halo"></span><span class="art" role="img" aria-label="Line illustration of apartment buildings"></span></div><h2>Property Management</h2><p>Every landlord needs a property management company.</p><a class="more" href="#">Learn More <svg width="8" height="8" viewBox="0 0 8 8"><path d="M1 1l3 3-3 3M4 1l3 3-3 3" fill="none" stroke="currentColor" stroke-width="1.3"/></svg></a></article>
  <article class="card"><div class="card-icon"><span class="halo"></span><span class="art" role="img" aria-label="Line illustration of a window"></span></div><h2>Window and Door Companies</h2><p>Window and door companies need local marketing more than ever.</p><a class="more" href="#">Learn More <svg width="8" height="8" viewBox="0 0 8 8"><path d="M1 1l3 3-3 3M4 1l3 3-3 3" fill="none" stroke="currentColor" stroke-width="1.3"/></svg></a></article>

  <article class="card"><div class="card-icon"><span class="halo"></span><span class="art" role="img" aria-label="Line illustration of an ambulance"></span></div><h2>Urgent Care Marketing</h2><p>Urgent care marketing is not just a field we are experts in but we are also very</p><a class="more" href="#">Learn More <svg width="8" height="8" viewBox="0 0 8 8"><path d="M1 1l3 3-3 3M4 1l3 3-3 3" fill="none" stroke="currentColor" stroke-width="1.3"/></svg></a></article>
  <article class="card"><div class="card-icon"><span class="halo"></span><span class="art" role="img" aria-label="Line illustration of a construction crane"></span></div><h2>Construction Companies</h2><p>We have deep knowledge of the construction industry.</p><a class="more" href="#">Learn More <svg width="8" height="8" viewBox="0 0 8 8"><path d="M1 1l3 3-3 3M4 1l3 3-3 3" fill="none" stroke="currentColor" stroke-width="1.3"/></svg></a></article>
  <article class="card"><div class="card-icon"><span class="halo"></span><span class="art" role="img" aria-label="Line illustration of caring hands for senior living"></span></div><h2>Senior Living Facilities</h2><p>Senior living facilities need marketing too and we have a long history of</p><a class="more" href="#">Learn More <svg width="8" height="8" viewBox="0 0 8 8"><path d="M1 1l3 3-3 3M4 1l3 3-3 3" fill="none" stroke="currentColor" stroke-width="1.3"/></svg></a></article>
</main>

<footer class="site-footer">
  <a class="foot-brand" href="#">
    <span class="brand-mark"></span>
    <span><div class="brand-name">TALL PINE</div><div class="brand-tag">GROWTH MARKETING</div></span>
  </a>
  <div class="social" aria-label="Social profiles"><span></span><span></span><span></span></div>

  <span class="divider" style="left:458px"></span>
  <span class="divider" style="left:726px"></span>

  <div class="foot-col links">
    <h3>Quick Links</h3>
    <ul><li>About Us</li><li>Our Industries</li><li>Our Services</li><li>Resources</li><li>Training</li><li>Blog</li></ul>
  </div>

  <div class="foot-col contact">
    <h3>Contact Info</h3>
    <div class="row"><svg width="18" height="18" viewBox="0 0 24 24"><path d="M12 2a7 7 0 0 0-7 7c0 5 7 13 7 13s7-8 7-13a7 7 0 0 0-7-7zm0 9.5A2.5 2.5 0 1 1 12 6.5a2.5 2.5 0 0 1 0 5z" fill="#8a1c22"/></svg><span>Address: 18 W. Elm Ave, Suite<br>300, Mesa, 85201</span></div>
    <div class="row"><svg width="18" height="18" viewBox="0 0 24 24"><rect x="2" y="5" width="20" height="14" rx="2" fill="#8a1c22"/><path d="M3 6l9 7 9-7" fill="none" stroke="#232323" stroke-width="1.6"/></svg><span>sales@tallpine.agency</span></div>
    <div class="row"><svg width="18" height="18" viewBox="0 0 24 24"><path d="M6.6 10.8a15 15 0 0 0 6.6 6.6l2.2-2.2a1 1 0 0 1 1-.25 11.4 11.4 0 0 0 3.6.57 1 1 0 0 1 1 1V20a1 1 0 0 1-1 1A17 17 0 0 1 3 4a1 1 0 0 1 1-1h3.5a1 1 0 0 1 1 1c0 1.25.2 2.45.57 3.57a1 1 0 0 1-.25 1z" fill="#8a1c22"/></svg><span class="tel">(480) 555-0142</span></div>
  </div>

  <div class="footbar">
    <span>© 2024 Tall Pine. All Rights Reserved.</span>
    <span class="legal"><span>Privacy</span><span>|</span><span>Terms</span><span>|</span><span>Disclaimer</span></span>
  </div>
</footer>

</body>
</html>
```